Harborline Lending and Capital. We provide MOSTLY residential home mortgages in Florida AND commercial loans for investment properties throughout the United states.
I would love to emulate so of the lender sites that are available on the internet but I would like to have the site as popular as possible for SEO purposes. Clients can already click the link to take them to the mortgage application where they can complete that and upload documents. If you could polish that up for me that would be great. I can also provide you with great detail on loan programs that are currently being offered. WE OFFER ALL MORTGAGE LENDING PRODUCTS. I would also like to add something in reference to the rate but I don't think it's legal to actually state or promise a rate for mortgage since they vary based on loan type, client and other criteria...

On the Harborline real estate site I would like to add a link or some way for clients to be able to put in credit card information to render services ...

Please let me know what you need from me

Thank you !!

Current link to site to improve and code

https://harborlinelendingandcapital.example/

Industry/Entity Type

Residential and commmercial lending

Coding

Coded - Design and coding required

Number of Pages Required

2 page

Requirements
Must have
• Love to integrate Mortgage interest rates even if general
Nice to have
• Link to fill out mortgage application via Quorvel LPX software

```html
<!DOCTYPE html>
<html lang="en">
<head>
<meta charset="utf-8">
<title>Harborline Lending and Capital</title>
<link href="https://fonts.googleapis.com/css2?family=Lexend:wght@400;500;600;700&family=Roboto:wght@400;500;700&display=swap" rel="stylesheet">
<style>
:root{
  --forest:#1b3118;
  --forest-2:#24401f;
  --lime:#8bb82e;
  --lime-2:#7aa524;
  --lime-3:#9cc63a;
  --ink:#222;
  --muted:#666;
  --line:#c9c9c9;
  --white:#fff;
}
*{box-sizing:border-box;margin:0;padding:0}
html,body{width:1200px;height:4441px;overflow:hidden;background:var(--white)}
body{position:relative;font-family:Roboto,Arial,sans-serif;color:var(--ink)}
.abs{position:absolute}
.display{font-family:Lexend,sans-serif;font-weight:600;letter-spacing:-.5px}
.accent{color:var(--lime)}
.mark{display:block;width:44px;height:11px;margin:0 auto 10px}
.mark::before,.mark::after{content:"";display:block;height:4px;background:var(--lime);border-radius:2px}
.mark::before{width:44px;margin-bottom:3px}
.mark::after{width:30px;margin:0 auto}
.mark.left{margin:0 0 10px}
.mark.left::after{margin:0}
.btn{position:absolute;display:flex;align-items:center;justify-content:center;border-radius:30px;font-family:Lexend,sans-serif;font-weight:500;font-size:14px;color:var(--white);background:var(--lime);text-transform:uppercase}
.btn.dark{background:var(--forest)}

/* header */
.logo-badge{left:112px;top:-70px;width:172px;height:172px;border-radius:50%;background:var(--white);z-index:3;display:flex;align-items:flex-end;justify-content:center;padding-bottom:28px}
.logo-badge span{width:70px;height:70px;border-radius:50%;background:var(--forest)}
.brand{left:266px;top:52px;z-index:3;font-family:Lexend,sans-serif;font-weight:600;font-size:9px;color:var(--forest);letter-spacing:.3px}
.brand small{display:block;font-weight:600;font-size:7px;letter-spacing:3px;margin-top:5px}
.search{left:690px;top:8px;width:232px;height:28px;border-bottom:1px solid var(--line);font-size:11px;color:#444;padding:6px 6px}
.search svg{position:absolute;right:8px;top:8px}
.socials{display:flex;gap:6px}
.socials i{width:28px;height:28px;border-radius:50%;border:2px solid var(--lime);display:block}
.socials.top{left:952px;top:11px}
.socials.top i:nth-child(2){border-color:var(--lime)}
.socials.top i:last-child{background:var(--lime)}
.nav{left:543px;top:48px;width:657px;height:50px;background:var(--forest);border-radius:26px 0 0 26px;z-index:2;display:flex;align-items:center;font-family:Lexend,sans-serif;font-weight:500;font-size:12px;color:var(--white)}
.nav a{padding:0 13px;color:inherit;text-decoration:none}
.nav a.active{background:var(--lime);height:50px;display:flex;align-items:center;padding:0 24px;border-radius:26px 0 0 26px;margin-right:6px}

/* hero */
.hero{left:0;top:98px;width:1200px;height:505px;background:linear-gradient(180deg,#3b5a86 0%,#7c8aa0 40%,#4d5a66 70%,#1e2b34 100%);overflow:hidden}
.hero h1{left:143px;top:105px;font-size:34px;line-height:43px;color:var(--white);text-transform:uppercase}
.hero h1 .accent{color:var(--lime);-webkit-text-stroke:0}
.hero p{left:143px;top:246px;width:560px;font-family:Lexend,sans-serif;font-weight:500;font-size:18px;line-height:26px;color:var(--white);text-transform:uppercase}
.hero .btn{left:141px;top:316px;width:583px;height:52px;font-size:18px;border:2px solid #b7d96a}
.dots{left:1131px;top:248px;display:flex;flex-direction:column;gap:12px}
.dots i{width:9px;height:9px;border-radius:50%;background:var(--white);display:block}
.dots i:nth-child(2){background:var(--lime)}
.hero-curve{left:0;top:540px;width:1200px;height:64px}
.scroll{left:588px;top:569px;width:24px;height:56px}

/* about */
.about-emblem{left:170px;top:680px;width:320px;height:400px;border-radius:50% 50% 44% 44%;background:radial-gradient(circle at 50% 60%,var(--forest-2),var(--forest));display:flex;align-items:center;justify-content:center}
.about-emblem span{font-family:Lexend,sans-serif;font-weight:600;color:var(--white);font-size:26px;text-align:center;line-height:34px}
.about{left:574px;top:670px;width:466px}
.about h2{font-size:37px;line-height:49px;color:var(--forest);text-transform:uppercase}
.about p{margin-top:16px;font-size:13.5px;line-height:25.5px;color:var(--muted);text-align:justify}

/* loan programs */
.programs{left:9px;top:1150px;width:1182px;height:612px;border-radius:306px;background:var(--lime-2);}
.programs-inner{left:24px;top:1170px;width:1152px;height:580px;border-radius:290px;background:var(--lime)}
.programs-title{left:0;top:1234px;width:1200px;text-align:center;font-size:36px;color:var(--white)}
.card{top:1334px;width:297px;height:252px;border-radius:22px;overflow:hidden;display:flex;align-items:flex-end;justify-content:center;padding-bottom:32px;font-family:Lexend,sans-serif;font-weight:500;font-size:13px;color:var(--white);text-transform:uppercase}
.card.c1{left:143px;background:linear-gradient(160deg,#8a97a8,#4d5358 55%,#2a2a2a)}
.card.c2{left:452px;background:linear-gradient(160deg,#4b4a50,#2f2c30 60%,#1e1c1f);padding:14px;align-items:stretch}
.card.c3{left:759px;background:linear-gradient(160deg,#b9c0c8,#6e6a6a 55%,#3a2f2c)}
.card.c2 .frame{border:2px solid rgba(255,255,255,.85);border-radius:16px;width:100%;text-align:center;padding-top:36px;text-transform:none}
.card.c2 h3{font-family:Lexend,sans-serif;font-weight:600;font-size:21px;line-height:25px;text-transform:uppercase}
.card.c2 p{font-family:Roboto,Arial,sans-serif;font-size:13px;line-height:17px;margin:12px 18px 12px;color:#eee}
.card.c2 a{font-size:11px;color:var(--lime);text-decoration:underline}
.programs .btn,.load-more{left:529px;top:1624px;width:141px;height:52px}

/* products */
.sec-title{left:0;width:1200px;text-align:center;font-size:37px;color:var(--forest);text-transform:uppercase}
.ring{left:0;top:0}
.feat{font-family:Roboto,Arial,sans-serif;font-weight:500;font-size:16px;line-height:26px;color:var(--ink)}
.feat.l{text-align:right}
.ico{width:82px;height:82px;border-radius:50%;display:flex;align-items:center;justify-content:center}
.ico.g{background:var(--lime)}
.ico.d{background:var(--forest)}
.hub{left:470px;top:2039px;width:260px;height:260px;border-radius:50%;background:var(--white);box-shadow:0 0 18px rgba(0,0,0,.12);display:flex;align-items:center;justify-content:center}
.hub span{width:150px;height:150px;border-radius:50%;background:var(--forest);display:flex;align-items:center;justify-content:center;font-family:Lexend,sans-serif;font-weight:600;color:var(--white);font-size:18px;text-align:center;line-height:22px}

/* rates */
.rates{left:143px;top:2469px;width:912px;height:355px;border-radius:178px;background:var(--forest)}
.rates-title{left:0;top:2513px;width:1200px;text-align:center;font-size:36px;color:var(--white)}
.rate-table{left:279px;top:2612px;width:642px;border-collapse:collapse;font-size:13.5px;color:var(--white)}
.rate-table td{height:43px;border:1px solid #6f7e6c;padding:0 22px 0 38px}
.rate-table td:first-child{color:var(--lime);width:186px}
.rate-table td:nth-child(2){width:176px}
.rate-table td+td{border-left:2px solid var(--white)}
.rates-btn{left:509px;top:2724px;width:182px;height:53px;font-size:13px}

/* properties */
.prop{width:278px;height:276px}
.prop-label{font-family:Lexend,sans-serif;font-weight:500;font-size:16px;color:var(--ink);text-transform:uppercase;display:flex;align-items:center;gap:22px}
.arrow-btn{width:30px;height:30px;border-radius:50%;background:var(--white);box-shadow:0 0 6px rgba(0,0,0,.25);display:flex;align-items:center;justify-content:center}

/* contact */
.contact-band{left:340px;top:3598px;width:860px;height:581px;background:var(--forest)}
.skyline{left:780px;top:3490px;width:420px;height:110px;background:linear-gradient(180deg,rgba(27,49,24,0) 0%,rgba(27,49,24,.55) 45%,var(--forest) 100%)}
.photo-circle{left:-12px;top:3618px;width:540px;height:540px;border-radius:50%;border:10px solid var(--white);background:linear-gradient(160deg,#9ac3e4 0%,#cfd9de 35%,#6d8d55 62%,#3f6d72 82%,#2f4e5a 100%)}
.contact h2{font-size:36px;color:var(--white);text-transform:uppercase}
.contact p{font-size:14px;color:var(--white);margin-top:10px}
.field{position:absolute;font-size:12px;color:var(--white);border-bottom:1px solid #b9c2b6;padding-bottom:10px}
.submit{left:579px;top:4031px;width:159px;height:53px;font-size:14px}

/* footer */
.foot-art{left:0;top:4310px;width:1200px;height:131px;background:linear-gradient(180deg,rgba(230,230,230,0),#f1f1f1)}
.finfo{display:flex;align-items:center;gap:14px;font-size:14px;color:var(--ink)}
.fi{width:40px;height:40px;border-radius:50%;border:2px solid var(--forest);display:flex;align-items:center;justify-content:center}
.fi.g{background:var(--lime);border-color:var(--lime)}
.copy{left:0;top:4324px;width:1200px;text-align:center;font-size:14px;color:var(--ink)}
.socials.foot{left:551px;top:4377px}
.socials.foot i{border:2px solid var(--forest);width:28px;height:28px}
.socials.foot i:nth-child(2){background:none}
.socials.foot i:nth-child(odd){background:var(--forest)}
</style>
</head>
<body>

<!-- header -->
<div class="abs logo-badge"><span></span></div>
<div class="abs brand">HARBORLINE LENDING AND CAPITAL<small>BUSINESS AND COMMERCIAL DIVISION</small></div>
<div class="abs search">Search
  <svg width="12" height="12" viewBox="0 0 12 12"><circle cx="5" cy="5" r="3.6" fill="none" stroke="#8bb82e" stroke-width="1.8"/><line x1="7.6" y1="7.6" x2="11" y2="11" stroke="#8bb82e" stroke-width="1.8"/></svg>
</div>
<div class="abs socials top" role="img" aria-label="Social media links"><i></i><i></i><i></i></div>
<nav class="abs nav">
  <a class="active">HOME</a><a>ABOUT</a><a>PROPERTIES</a><a>PROGRAMS</a><a>PRODUCTS</a><a>CONTACT</a>
</nav>

<!-- hero -->
<section class="abs hero" role="img" aria-label="Downtown city skyline by the river at dusk">
  <h1 class="abs display">Residential home loans in<br>Florida and <span class="accent">commercial lending</span><br>in America</h1>
  <p class="abs">Your best resource for hassle-free, low cost<br>mortgage origination</p>
  <div class="btn">Fill out mortgage application to begin lending pr</div>
  <div class="abs dots"><i></i><i></i><i></i></div>
</section>
<svg class="abs hero-curve" viewBox="0 0 1200 64" preserveAspectRatio="none">
  <path d="M318 64 Q600 -20 882 64 Z" fill="#8bb82e"/>
  <path d="M335 64 Q600 -6 865 64 Z" fill="#fff"/>
</svg>
<svg class="abs scroll" viewBox="0 0 24 56">
  <rect x="4" y="1" width="16" height="26" rx="8" fill="#fff" stroke="#333" stroke-width="1.5"/>
  <line x1="12" y1="7" x2="12" y2="13" stroke="#333" stroke-width="2"/>
  <path d="M5 32 l7 6 7-6 M5 39 l7 6 7-6 M5 46 l7 6 7-6" fill="none" stroke="#333" stroke-width="1.5"/>
</svg>

<!-- about -->
<div class="abs about-emblem" role="img" aria-label="Harborline Lending and Capital emblem"><span>Harborline<br>Lending<br>and Capital</span></div>
<section class="abs about">
  <span class="mark left"></span>
  <h2 class="display">About Harborline<br><span class="accent">Lending and Capital</span></h2>
  <p>Harborline Lending originates residential home loans in Florida and commercial and business financing in all 50 States. We have over 25 years of experience in ALL types of real estate and commercial lending. We are strategically partnered to help you obtain ALL necessary components of residential and commercial lending. From the RIGHT lending partners to the best practice Insurance avenues and commercial and residential real estate partners</p>
</section>
<div class="btn" style="left:574px;top:1002px;width:140px;height:53px;font-size:13px">Read more</div>

<!-- loan programs -->
<div class="abs programs"></div>
<div class="abs programs-inner"></div>
<div class="abs" style="left:0;top:1232px;width:1200px"><span class="mark" style="filter:brightness(3)"></span></div>
<h2 class="abs programs-title display" style="top:1252px">LOAN PROGRAMS</h2>
<div class="abs card c1" role="img" aria-label="Home model on mortgage paperwork">Residential mortgages</div>
<div class="abs card c2" role="img" aria-label="Stacked coins with a small house">
  <div class="frame"><h3>Investment<br>loans</h3><p>Sed ut perspiciatis unde omnis iste natus error sit voluptatem</p><a>READ MORE</a></div>
</div>
<div class="abs card c3" role="img" aria-label="Advisors reviewing documents on a tablet">Specialty loans</div>
<div class="btn dark" style="left:529px;top:1624px;width:141px;height:52px;font-size:13px">Load more</div>

<!-- products -->
<div class="abs" style="left:0;top:1854px;width:1200px"><span class="mark"></span></div>
<h2 class="abs sec-title display" style="top:1874px">Mortgage lending <span class="accent">products</span></h2>
<svg class="abs" style="left:425px;top:1994px" width="350" height="350" viewBox="0 0 350 350">
  <circle cx="175" cy="175" r="171" fill="none" stroke="#8bb82e" stroke-width="2"/>
  <g fill="#fff" stroke="#1b3118" stroke-width="2.5">
    <circle cx="53" cy="59" r="7"/><circle cx="297" cy="59" r="7"/>
    <circle cx="6" cy="174" r="7"/><circle cx="344" cy="174" r="7"/>
    <circle cx="53" cy="290" r="7"/><circle cx="297" cy="290" r="7"/>
  </g>
</svg>
<div class="abs hub" style="left:470px;top:2039px"><span>Harborline<br>Lending</span></div>

<div class="abs feat l" style="left:150px;top:1994px;width:215px">Sed ut perspiciatisu<br>nde omnis iste</div>
<div class="abs ico d" style="left:378px;top:1981px"><svg width="40" height="40" viewBox="0 0 40 40" fill="none" stroke="#fff" stroke-width="2"><path d="M5 19 L20 6 35 19 M10 15 V34 H30 V15"/><circle cx="20" cy="24" r="5"/></svg></div>

<div class="abs feat l" style="left:80px;top:2142px;width:220px">Nemo enim ipsam<br>tatemluptas sit</div>
<div class="abs ico g" style="left:309px;top:2131px"><svg width="40" height="40" viewBox="0 0 40 40" fill="none" stroke="#fff" stroke-width="2"><path d="M5 19 L20 6 35 19 M10 15 V34 H30 V15"/><path d="M16 26 h8 M20 22 v8"/></svg></div>

<div class="abs feat l" style="left:150px;top:2305px;width:220px">Ut enim ad minima<br>umquam veniam</div>
<div class="abs ico d" style="left:383px;top:2281px"><svg width="40" height="40" viewBox="0 0 40 40" fill="none" stroke="#fff" stroke-width="2"><circle cx="12" cy="12" r="4"/><circle cx="28" cy="12" r="4"/><path d="M5 28 q7-10 14 0 M21 28 q7-10 14 0"/><circle cx="20" cy="30" r="5"/></svg></div>

<div class="abs ico g" style="left:749px;top:1981px"><svg width="40" height="40" viewBox="0 0 40 40" fill="none" stroke="#fff" stroke-width="2"><path d="M5 19 L20 6 35 19 M10 15 V34 H30 V15"/><path d="M15 29 L25 19"/><circle cx="16" cy="21" r="2"/><circle cx="24" cy="27" r="2"/></svg></div>
<div class="abs feat" style="left:841px;top:1994px;width:220px">Neque porro quisqu<br>am eui dolorem</div>

<div class="abs ico d" style="left:795px;top:2131px"><svg width="40" height="40" viewBox="0 0 40 40" fill="none" stroke="#fff" stroke-width="2"><path d="M5 17 L20 5 35 17 M9 14 V34 H31 V14"/><rect x="14" y="20" width="12" height="9"/></svg></div>
<div class="abs feat" style="left:887px;top:2142px;width:220px">Neque porroisquam<br>estqui dolorem</div>

<div class="abs ico g" style="left:749px;top:2281px"><svg width="40" height="40" viewBox="0 0 40 40" fill="none" stroke="#fff" stroke-width="2"><circle cx="12" cy="13" r="5"/><path d="M4 32 q8-14 16 0"/><path d="M22 18 L30 11 38 18 V32 H22 Z"/></svg></div>
<div class="abs feat" style="left:846px;top:2305px;width:220px">Sed quia consequuntur<br>magni dolores eos</div>

<!-- rates -->
<div class="abs rates"></div>
<div class="abs" style="left:0;top:2513px;width:1200px"><span class="mark"></span></div>
<h2 class="abs rates-title display" style="top:2533px">MORTGAGE INTEREST RATES</h2>
<table class="abs rate-table">
  <tr><td>Conventional Loan</td><td>Starting at 6.5% APR</td><td>Great for well-qualified borrowers.</td></tr>
  <tr><td>FHA Loan</td><td>Starting at 6.0% APR</td><td>Ideal for first-time homebuyers.</td></tr>
</table>
<div class="btn rates-btn">View more rates</div>

<!-- properties -->
<div class="abs" style="left:0;top:2922px;width:1200px"><span class="mark"></span></div>
<h2 class="abs sec-title display" style="top:2942px">Available&nbsp; <span class="accent">properties</span></h2>

<div class="abs prop" style="left:31px;top:3091px;background:linear-gradient(160deg,#8fb6d6 0%,#d9d9d9 30%,#f1f1f1 60%,#bdbdbd 100%)" role="img" aria-label="White modern house facade"></div>
<div class="abs prop-label" style="left:72px;top:3384px">12 Sunset Street<svg width="20" height="16" viewBox="0 0 20 16" fill="none" stroke="#8bb82e" stroke-width="2.5"><path d="M2 2l6 6-6 6M10 2l6 6-6 6"/></svg></div>

<div class="abs prop" style="left:317px;top:3045px;background:linear-gradient(160deg,#6f8a5c 0%,#2a3436 40%,#1a2022 75%,#7f7a6c 100%)" role="img" aria-label="Dark modern townhouses"></div>
<div class="abs" style="left:440px;top:3169px;width:30px;height:30px;border-radius:50%;background:#fff;display:flex;align-items:center;justify-content:center;font-size:18px;color:#1b3118">+</div>
<div class="abs prop-label" style="left:358px;top:3338px">34 Union Avenue<svg width="20" height="16" viewBox="0 0 20 16" fill="none" stroke="#8bb82e" stroke-width="2.5"><path d="M2 2l6 6-6 6M10 2l6 6-6 6"/></svg></div>

<div class="abs prop" style="left:603px;top:3091px;background:linear-gradient(180deg,#9ab8d6 0%,#e8e8e8 30%,#9d7b5a 60%,#1c9ec2 82%,#38b3d4 100%)" role="img" aria-label="House with swimming pool"></div>
<div class="abs prop-label" style="left:622px;top:3384px">56 Washington Street<svg width="20" height="16" viewBox="0 0 20 16" fill="none" stroke="#8bb82e" stroke-width="2.5"><path d="M2 2l6 6-6 6M10 2l6 6-6 6"/></svg></div>

<div class="abs prop" style="left:890px;top:3045px;background:linear-gradient(120deg,#8c3d2a 0%,#6b2f22 45%,#2c3240 70%,#5f8fd0 100%)" role="img" aria-label="Brick and glass building facade"></div>
<div class="abs prop-label" style="left:931px;top:3338px">78 Oak Boulevard<svg width="20" height="16" viewBox="0 0 20 16" fill="none" stroke="#8bb82e" stroke-width="2.5"><path d="M2 2l6 6-6 6M10 2l6 6-6 6"/></svg></div>

<div class="abs arrow-btn" style="left:18px;top:3214px"><svg width="10" height="14" viewBox="0 0 10 14" fill="none" stroke="#222" stroke-width="2"><path d="M8 1L2 7l6 6"/></svg></div>
<div class="abs arrow-btn" style="left:1150px;top:3214px"><svg width="10" height="14" viewBox="0 0 10 14" fill="none" stroke="#222" stroke-width="2"><path d="M2 1l6 6-6 6"/></svg></div>
<div class="btn" style="left:520px;top:3457px;width:160px;height:52px;font-size:13px">View more</div>

<!-- contact -->
<div class="abs skyline" role="img" aria-label="City skyline silhouette"></div>
<div class="abs contact-band"></div>
<div class="abs photo-circle" role="img" aria-label="Waterfront marina with palm trees and high-rise buildings"></div>
<section class="abs contact" style="left:579px;top:3688px;width:470px">
  <span class="mark left"></span>
  <h2 class="display">Get in touch</h2>
  <p>Please send me a message for general inquiries or reservations.</p>
</section>
<div class="field" style="left:579px;top:3818px;width:221px">First Name</div>
<div class="field" style="left:827px;top:3818px;width:221px">Last Name</div>
<div class="field" style="left:579px;top:3882px;width:221px">Email Address</div>
<div class="field" style="left:827px;top:3882px;width:221px">Phone Number</div>
<div class="field" style="left:579px;top:3946px;width:469px;height:62px">Message</div>
<div class="btn submit">Submit</div>

<!-- footer -->
<div class="abs foot-art" role="img" aria-label="Faint city line drawing"></div>
<div class="abs finfo" style="left:256px;top:4252px">
  <span class="fi"><svg width="14" height="18" viewBox="0 0 14 18" fill="#1b3118"><path d="M7 0a7 7 0 0 0-7 7c0 5 7 11 7 11s7-6 7-11a7 7 0 0 0-7-7zm0 9.5A2.5 2.5 0 1 1 7 4.5a2.5 2.5 0 0 1 0 5z"/></svg></span>
  <span style="font-size:13px;line-height:19px">233,sed quia consequuntur<br>magni dolores eos qui</span>
</div>
<div class="abs finfo" style="left:517px;top:4252px">
  <span class="fi g"><svg width="16" height="16" viewBox="0 0 16 16" fill="#fff"><path d="M3.5 1l2.5 3-1.5 2c1 2 3 4 5 5l2-1.5 3 2.5-1.5 2.5C7 14.5 1.5 9 1 3z"/></svg></span>
  <span style="font-weight:500">+1 888 888 8888</span>
</div>
<div class="abs finfo" style="left:730px;top:4252px">
  <span class="fi"><svg width="16" height="12" viewBox="0 0 16 12" fill="#1b3118"><path d="M0 0h16v12H0z"/><path d="M1 1l7 5 7-5" stroke="#fff" stroke-width="1.3" fill="none"/></svg></span>
  <span>info@companyname.com</span>
</div>
<div class="abs copy">Copyright 2025 Harborline Real Estate.All Rights Reserved &nbsp;|&nbsp; Privacy Policy</div>
<div class="abs socials foot" role="img" aria-label="Social media links"><i></i><i></i><i></i></div>

</body>
</html>
```